Development of musical artist Tavro Quill's Website

I need a website designed for a reggae musical artist by the name of Tavro Quill. The site should be representative of a Reggae artist from Jamaica that has a Caribbean appeal but also attractive to global audiences. The website should be responsive for all devices (desktop, laptop, mobile). It should be optimized for SEO purposes. Icons for Photoshare, Friendbook, Chirper, VideoHub should be included. The sections of the website should be as follows: Home, Media, News, Bio, Join, Contact. The 'Join' section should be a form for database collection to the fan club. I would like to easily be able to dump this database in an excel or .csv file at any given time. The 'Media' section should be able to showcase video thumbnails and allow persons to play videos through the site and the videos will be fed from VideoHub. The 'News' section will be for announcements and or new releases where the artist is mentioned. The site should also be built in such a way that analytics can be easily implemented. This website should be the main call to action for this artist moving forward. I would also like the website to have a easy to use CMS platform (Wordpress perhaps). The URL for the website will be tavroquillstar.example. Here are the links for some of the social media pages:
VideoHub - https://www.videohub.example/user/TavroQuill
Photoshare - https://www.photoshare.example/tavroquill/
A good website to refer to from a design perspective is https://marvello.example/

Target Market(s)

Reggae and Pop music fans

Industry/Entity Type

Artists

Coding

Number of Pages Required

5+ page

Font styles to use
Sans Serif

Requirements
Must have
• Great design
Nice to have
• Parallax technology

```html
<!DOCTYPE html>
<html lang="en">
<head>
<meta charset="utf-8">
<title>Tavro Quill — Official Site</title>
<link rel="stylesheet" href="https://fonts.googleapis.com/css2?family=Lato:ital,wght@0,400;0,700;0,900;1,400&family=Kaushan+Script&family=Open+Sans:wght@400;600&display=swap">
<style>
:root{
  --ink:#1c1c1c;
  --nav:#2a2d31;
  --red:#c8000b;
  --red-deep:#a10008;
  --grey-band:#dcdcdc;
  --dark-band:#141414;
  --white:#ffffff;
  --muted:#6d6d6d;
  --footer:#3a3a3a;
}
*{margin:0;padding:0;box-sizing:border-box}
html,body{width:1200px;height:3666px;overflow:hidden}
body{position:relative;background:var(--white);font-family:"Lato",Arial,sans-serif;color:var(--ink)}
.abs{position:absolute}
.bands{position:absolute;left:0;top:0;width:1200px;height:3666px}

/* nav */
.site-nav{position:absolute;left:0;top:0;width:1200px;height:100px;background:var(--nav);opacity:.96}
.brand{position:absolute;left:161px;top:38px;display:flex;align-items:center;gap:12px;color:var(--white);font-weight:900;font-size:30px;letter-spacing:1px}
.brand-dot{width:16px;height:16px;border-radius:50%;background:var(--red)}
.menu{position:absolute;top:48px;left:0;list-style:none;font-family:"Lato",sans-serif;font-weight:700;font-size:18px;color:var(--white)}
.menu li{position:absolute;white-space:nowrap;letter-spacing:.5px}

/* hero */
.hero-photo{position:absolute;left:0;top:0;width:1200px;height:745px;clip-path:polygon(0 0,100% 0,100% 665px,0 745px);
  background:radial-gradient(ellipse at 55% 45%,#7a5a45 0%,#4a4d52 38%,#5f7f98 70%,#86a4bd 100%)}
.hero-title{position:absolute;left:0;width:1200px;text-align:center;color:var(--white);font-family:"Kaushan Script",cursive}
.hero-welcome{top:292px;font-size:46px;letter-spacing:2px}
.hero-name{top:340px;font-size:92px;letter-spacing:3px}
.dots{position:absolute;top:664px;left:562px;display:flex;gap:10px}
.dots span{width:14px;height:14px;border-radius:50%;border:2px solid var(--white)}
.dots span.on{background:var(--white)}

/* headings */
.section-title{position:absolute;left:0;width:1200px;text-align:center;font-family:"Lato",sans-serif;font-weight:900;font-size:38px;letter-spacing:2px}
.section-title.light{color:var(--white)}

/* media */
.thumb{position:absolute;width:278px;height:184px}
.play{position:absolute;left:50%;top:50%;width:46px;height:46px;margin:-23px 0 0 -23px;border-radius:50%;background:rgba(255,255,255,.85);border:2px solid #fff}
.play::after{content:"";position:absolute;left:17px;top:12px;border-left:15px solid #333;border-top:9px solid transparent;border-bottom:9px solid transparent}

/* news */
.news-card{position:absolute;top:1493px;width:281px;height:343px;background:var(--white);border:1px solid #c9c9c9}
.news-photo{height:184px}
.news-body{padding:12px 22px 0}
.news-date{color:var(--red);font-size:14px}
.news-title{font-size:17px;font-weight:700;margin-top:6px;text-transform:uppercase}
.news-excerpt{font-family:"Open Sans",sans-serif;font-size:11px;line-height:15px;color:var(--muted);margin-top:6px}
.news-more{font-size:10px;font-weight:700;margin-top:10px;letter-spacing:.5px}

/* bio */
.bio-photo{position:absolute;left:0;top:1960px;width:800px;height:560px;
  background:linear-gradient(90deg,#2a1a14 0%,#4a2d22 45%,#23160f 75%,rgba(20,20,20,0) 100%)}
.bio-title{position:absolute;left:565px;top:2068px;color:var(--white);font-weight:900;font-size:38px;letter-spacing:2px}
.bio-text{position:absolute;left:565px;top:2128px;width:500px;color:#e8e8e8;font-family:"Open Sans",sans-serif;font-size:15.5px;line-height:21px}
.bio-text p+p{margin-top:10px}

/* join */
.field{position:absolute;height:44px;border:1.5px solid #f2f2f2;color:var(--white);font-size:15px;padding:12px 18px}
.field.message{height:100px}
.submit{position:absolute;left:513px;top:2879px;width:167px;height:46px;background:#0c0c0c;color:var(--white);font-weight:900;font-size:17px;letter-spacing:1px;text-align:center;line-height:46px}

/* contact */
.contact-photo{position:absolute;left:560px;top:3010px;width:640px;height:500px;
  background:linear-gradient(90deg,rgba(255,255,255,1) 0%,rgba(215,210,205,.55) 45%,rgba(190,185,180,.45) 100%)}
.contact-item{position:absolute;top:3225px;width:300px;text-align:center}
.contact-item svg{display:block;margin:0 auto}
.contact-label{color:var(--red);font-weight:900;font-size:20px;margin-top:20px}
.contact-value{color:#4a4a4a;font-size:19px;line-height:32px;margin-top:6px;text-transform:uppercase}

/* footer */
.copyright{position:absolute;left:0;top:3574px;width:1200px;text-align:center;color:#dedede;font-size:14px;letter-spacing:.5px}
.socials{position:absolute;left:0;top:3612px;width:1200px;display:flex;justify-content:center;gap:26px;list-style:none}
.socials li{display:flex;align-items:center;gap:8px;color:#dedede;font-size:14px}
.socials li span{width:14px;height:14px;border-radius:50%;border:1.5px solid #bdbdbd}
</style>
</head>
<body>

<svg class="bands" viewBox="0 0 1200 3666" aria-hidden="true">
  <polygon points="0,1327 1200,1392 1200,1880 0,1975" fill="var(--grey-band)"/>
  <polygon points="0,1975 1200,1880 1200,2542 0,2480" fill="var(--dark-band)"/>
  <polygon points="0,2480 1200,2542 1200,2995 0,3067" fill="var(--red)"/>
  <polygon points="0,3515 1200,3497 1200,3666 0,3666" fill="var(--footer)"/>
</svg>

<div class="hero-photo" role="img" aria-label="Hero photograph of the artist in sunglasses and denim shirt against the sky"></div>

<header class="site-nav">
  <div class="brand"><span class="brand-dot"></span>TAVRO QUILL</div>
  <ul class="menu">
    <li style="left:521px">HOME</li>
    <li style="left:602px">MEDIA</li>
    <li style="left:700px">NEWS</li>
    <li style="left:792px">BIO</li>
    <li style="left:865px">JOIN</li>
    <li style="left:950px">CONTACT</li>
  </ul>
</header>

<div class="hero-title hero-welcome">WELCOME TO</div>
<div class="hero-title hero-name">TAVRO QUILL</div>
<div class="dots"><span></span><span class="on"></span><span></span></div>

<section class="media">
  <h2 class="section-title" style="top:768px">MEDIA</h2>
  <div class="thumb" style="left:161px;top:846px;background:linear-gradient(135deg,#5a4a3c,#2e2722)" role="img" aria-label="Video thumbnail: artist in studio"><span class="play"></span></div>
  <div class="thumb" style="left:463px;top:846px;background:linear-gradient(135deg,#8a5a2a,#3a2a1e)" role="img" aria-label="Video thumbnail: music video cover"><span class="play"></span></div>
  <div class="thumb" style="left:760px;top:846px;background:linear-gradient(135deg,#3f6b3a,#8a3a2a)" role="img" aria-label="Video thumbnail: performance clip"><span class="play"></span></div>
  <div class="thumb" style="left:161px;top:1058px;background:linear-gradient(135deg,#9a8a70,#4a4034)" role="img" aria-label="Video thumbnail: artist portrait clip"><span class="play"></span></div>
  <div class="thumb" style="left:463px;top:1058px;background:linear-gradient(135deg,#c2381e,#2a3a6a)" role="img" aria-label="Video thumbnail: collaboration single artwork"><span class="play"></span></div>
  <div class="thumb" style="left:760px;top:1058px;background:linear-gradient(135deg,#6a6a6a,#2a2a2a)" role="img" aria-label="Video thumbnail: keyboard session"><span class="play"></span></div>
</section>

<section class="news">
  <h2 class="section-title" style="top:1392px">NEWS</h2>
  <article class="news-card" style="left:154px">
    <div class="news-photo" role="img" aria-label="News photo: artist in red-lit studio" style="background:linear-gradient(135deg,#b0202a,#3a0a10)"></div>
    <div class="news-body">
      <div class="news-date">12 JAN 2019</div>
      <h3 class="news-title">News title here</h3>
      <p class="news-excerpt">Netus et malesuada fames ac turpis egestas Cras id elit integer quis urna Ut ante enim dapibus malesuada fringilla eu cond</p>
      <div class="news-more">READ MORE</div>
    </div>
  </article>
  <article class="news-card" style="left:457px">
    <div class="news-photo" role="img" aria-label="News photo: artist seated in a car" style="background:linear-gradient(135deg,#d8d4cc,#5a4a40)"></div>
    <div class="news-body">
      <div class="news-date">12 JAN 2019</div>
      <h3 class="news-title">News title here</h3>
      <p class="news-excerpt">Netus et malesuada fames ac turpis egestas Cras id elit integer quis urna Ut ante enim dapibus malesuada fringilla eu cond</p>
      <div class="news-more">READ MORE</div>
    </div>
  </article>
  <article class="news-card" style="left:760px">
    <div class="news-photo" role="img" aria-label="News photo: artist with a guest" style="background:linear-gradient(135deg,#6a4a3a,#d8b84a)"></div>
    <div class="news-body">
      <div class="news-date">12 JAN 2019</div>
      <h3 class="news-title">News title here</h3>
      <p class="news-excerpt">Netus et malesuada fames ac turpis egestas Cras id elit integer quis urna Ut ante enim dapibus malesuada fringilla eu cond</p>
      <div class="news-more">READ MORE</div>
    </div>
  </article>
</section>

<section class="bio">
  <div class="bio-photo" role="img" aria-label="Portrait photograph of the artist"></div>
  <h2 class="bio-title">BIO</h2>
  <div class="bio-text">
    <p>Mauris vel lacus vitae felis vestibulum volutpat Etiam est nunc venenatis in tristique eu imperdiet ac nisl Cum sociis natoque penatibus et magnis dis parturient montes nascetur ridiculus mus In iaculis facilisis massa Etiam eu urna Sed porta Suspendisse quam leo molestie sed luctus quis feugiat in pede</p>
    <p>Fusce tellus Sed metus augue convallis et vehicula ut pulvinar eu ante Integer orci tellus tristique vitae consequat nec porta vel lectus Nulla sit amet diam Duis non nunc Nulla rhoncus dictum metus Curabitur tristique mi condimentum orci Phasellus pellentesque</p>
  </div>
</section>

<section class="join">
  <h2 class="section-title light" style="top:2590px">JOIN</h2>
  <div class="field" style="left:227px;top:2654px;width:366px">First Name</div>
  <div class="field" style="left:604px;top:2654px;width:366px">Last Name</div>
  <div class="field" style="left:227px;top:2708px;width:366px">Email address</div>
  <div class="field" style="left:604px;top:2708px;width:366px">Phone Number</div>
  <div class="field message" style="left:227px;top:2764px;width:743px">Type Message</div>
  <div class="submit">SUBMIT</div>
</section>

<section class="contact">
  <div class="contact-photo" role="img" aria-label="Faded photograph of the artist behind the contact details"></div>
  <h2 class="section-title" style="top:3108px">CONTACT</h2>
  <div class="contact-item" style="left:155px">
    <svg width="44" height="60" viewBox="0 0 44 60"><path d="M22 57C12 42 4 32 4 21a18 18 0 0 1 36 0c0 11-8 21-18 36z" fill="none" stroke="var(--red)" stroke-width="3"/><circle cx="22" cy="21" r="7" fill="none" stroke="var(--red)" stroke-width="3"/></svg>
    <div class="contact-label">ADDRESS</div>
    <div class="contact-value">42 Harbor Lane #5B<br>Kingston Ridge 20417</div>
  </div>
  <div class="contact-item" style="left:446px">
    <svg width="56" height="60" viewBox="0 0 56 60"><path d="M10 6l10 0 5 13-7 5c4 9 10 15 18 19l5-7 13 5v10c0 3-3 6-6 6C26 57 3 33 4 12c0-3 3-6 6-6z" fill="none" stroke="var(--red)" stroke-width="3" stroke-linejoin="round"/></svg>
    <div class="contact-label">PHONE</div>
    <div class="contact-value">555.014.2871</div>
  </div>
  <div class="contact-item" style="left:727px">
    <svg width="64" height="60" viewBox="0 0 64 60"><rect x="4" y="10" width="56" height="42" fill="none" stroke="var(--red)" stroke-width="3"/><path d="M4 12l28 22 28-22" fill="none" stroke="var(--red)" stroke-width="3"/></svg>
    <div class="contact-label">EMAIL</div>
    <div class="contact-value">info@companyname.com</div>
  </div>
</section>

<footer>
  <p class="copyright">© 2019 COMPANY NAME &nbsp;ALL RIGHT RESERVED</p>
  <ul class="socials">
    <li><span></span>Chirper</li>
    <li><span></span>Friendbook</li>
    <li><span></span>VideoHub</li>
    <li><span></span>Photoshare</li>
  </ul>
</footer>

</body>
</html>
```